Card design for orthopaedic surgeons working as The Brightwater Joint Centre

Business cards, letterhead

Colors

Designer to choose colors to be used in the design.

Requirements
Must have
• Late addition.
• Cards letterhead must have logos of
• Crestmoor Lindell College of Surgeons
• Varenwood Bone Health Association
Nice to have
• Back of card to have space for appointment time to be added by hand and some blank space for writing incidental other notes.

```html
<!DOCTYPE html>
<html lang="en">
<head>
<meta charset="utf-8">
<title>The Brightwater Joint Centre – Business Card</title>
<link rel="stylesheet" href="https://fonts.googleapis.com/css2?family=Montserrat:wght@400&family=Roboto:wght@400;700&display=swap">
<style>
  :root {
    --backdrop: #b5b5b5;
    --sky: #54a8de;
    --navy: #05304a;
    --ink: #0f2b40;
    --paper: #ffffff;
  }
  * { box-sizing: border-box; margin: 0; padding: 0; }
  html, body { width: 1172px; height: 1200px; overflow: hidden; }
  body { background: var(--backdrop); position: relative; font-family: "Roboto", Arial, sans-serif; }

  .card {
    position: absolute;
    left: 214px;
    width: 744px;
    height: 428px;
    border-radius: 26px;
    overflow: hidden;
  }
  .card--front { top: 122px; background: var(--sky); }
  .card--back { top: 645px; background: var(--paper); }

  .brand-name {
    position: absolute;
    left: 0; right: 0;
    text-align: center;
    font-family: "Montserrat", Arial, sans-serif;
    font-weight: 400;
    font-size: 42px;
    line-height: 50px;
    letter-spacing: -0.6px;
    white-space: nowrap;
  }
  .card--front .brand-name { top: 210px; color: var(--paper); }
  .card--back .brand-name { top: 127px; color: var(--navy); }

  .person {
    position: absolute;
    right: 392px;
    top: 247px;
    text-align: right;
    white-space: nowrap;
  }
  .person__name { font-weight: 700; font-size: 29px; color: var(--sky); line-height: 34px; }
  .person__title { font-size: 20px; color: var(--ink); line-height: 28px; margin-top: 2px; }

  .divider {
    position: absolute;
    left: 376px; top: 240px;
    width: 2px; height: 80px;
    background: var(--navy);
  }

  .contact { position: absolute; left: 400px; top: 238px; list-style: none; }
  .contact__item {
    display: flex; align-items: center;
    height: 30px;
    font-size: 20.5px; color: var(--ink);
    white-space: nowrap;
  }
  .contact__icon { width: 15px; height: 15px; margin-right: 9px; flex: none; }

  .wave { position: absolute; left: 0; bottom: 0; width: 744px; height: 430px; }
</style>
</head>
<body>

  <section class="card card--front" aria-label="Card front">
    <p class="brand-name">The Brightwater Joint Centre</p>
  </section>

  <section class="card card--back" aria-label="Card back">
    <p class="brand-name">The Brightwater Joint Centre</p>

    <div class="person">
      <p class="person__name">Dr. Nolan Harwick</p>
      <p class="person__title">Orthopaedic Specialist</p>
    </div>

    <div class="divider"></div>

    <ul class="contact">
      <li class="contact__item">
        <svg class="contact__icon" viewBox="0 0 16 16" aria-hidden="true"><path d="M3.5 1.5 L6 4.5 L4.6 6.2 C5.6 8.2 7.6 10.2 9.8 11.4 L11.5 10 L14.5 12.5 L13 14.5 C7.5 14.5 1.5 8.5 1.5 3 Z" fill="none" stroke="#54a8de" stroke-width="1.5" stroke-linejoin="round"/><path d="M9.5 2 A4.5 4.5 0 0 1 14 6.5 M9.5 4.5 A2 2 0 0 1 11.5 6.5" fill="none" stroke="#54a8de" stroke-width="1.3"/></svg>
        622-555-0148
      </li>
      <li class="contact__item">
        <svg class="contact__icon" viewBox="0 0 16 16" aria-hidden="true"><rect x="1" y="3" width="14" height="10" fill="#54a8de"/><path d="M1 3 L8 9 L15 3" fill="none" stroke="#fff" stroke-width="1.2"/></svg>
        info@brightwaterjoint.com
      </li>
      <li class="contact__item">
        <svg class="contact__icon" viewBox="0 0 16 16" aria-hidden="true"><circle cx="8" cy="8" r="7" fill="#54a8de"/><path d="M4 5 C6 4 7 6 6 8 C5 10 7 11 7 13 M11 3 C10 5 12 6 13 7 M10 10 C11 11 12 11 12.5 10" fill="none" stroke="#fff" stroke-width="1.3"/></svg>
        www.brightwaterjoint.com
      </li>
    </ul>

    <svg class="wave" viewBox="0 0 744 430" aria-hidden="true">
      <path d="M0 393 C70 355 150 347 240 356 C360 368 500 420 640 416 C700 414 744 400 744 380 L744 430 L0 430 Z" fill="#05304a"/>
      <path d="M330 362 C470 398 610 418 744 362 L744 377 C620 425 470 408 330 362 Z" fill="#ffffff"/>
      <path d="M326 363 C460 392 620 408 744 348 L744 364 C610 412 470 400 326 363 Z" fill="#54a8de"/>
    </svg>
  </section>

</body>
</html>
```